We need a business card for our gym. We are a PowerCore affiliate in Decatur Georgie established 2008. Our company name is Rally Functional Fitness. PowerCore Building Prime Fitness. Instagram and website is @rallygym. Hashtags we use #rallywithheart #madetorally We want something similar to the the black and neon green design attached but a different color scheme. No neon colors. Are company colors are the same as the blue and white card attached. We are open to ideas as far as colors however - just no neon.

Contact Information for Business Card

Rally Functional Fitness
472 Halvern Drive
Decatur GA 30041
Phone 404.555.0187 Website www.rallygym.example

Font styles to use
Other font styles liked:
• Futura Extra Bold Condensed

Colors

Designer to choose colors to be used in the design.

Requirements
Must have
• Our primary font we typically use for our name is Futura Extra Bold Condensed
Nice to have
• I attached a card from that is black and neon green from Zorva that we would like something similar. The blue and white is more similar to our colors. We also use have used black and white in the past. We use the chevrons as out logo. We are a PowerCore affiliate so I included a logo from them as well that may or may not be used on the card. Our instagram is @rallygym hashtags #madetorally #rallywithheart
Should not have
• No neon colors

```html
<!DOCTYPE html>
<html lang="en">
<head>
<meta charset="utf-8">
<title>Rally Functional Fitness – Business Card</title>
<link href="https://fonts.googleapis.com/css2?family=Anton&family=Montserrat:wght@400;500&display=swap" rel="stylesheet">
<style>
  :root {
    --brand-blue: #135c9a;
    --card-white: #ffffff;
    --backdrop: #d2d2d2;
    --rule-blue: #3f6fae;
    --card-shadow: rgba(0, 0, 0, 0.18);
  }
  * { box-sizing: border-box; margin: 0; padding: 0; }
  html, body {
    width: 1200px;
    height: 800px;
    overflow: hidden;
    background: var(--backdrop);
  }
  .canvas {
    position: relative;
    width: 1200px;
    height: 800px;
  }
  .card {
    position: absolute;
    width: 525px;
    height: 300px;
    box-shadow: 0 4px 14px var(--card-shadow);
  }

  /* Front side */
  .card--front {
    left: 70px;
    top: 90px;
    background: var(--brand-blue);
  }
  .card--front .wordmark {
    position: absolute;
    right: 44px;
    top: 96px;
    color: var(--card-white);
  }

  /* Back side */
  .card--back {
    left: 605px;
    top: 410px;
    background: var(--card-white);
  }
  .card--back .wordmark {
    position: absolute;
    left: 40px;
    top: 108px;
    color: var(--brand-blue);
  }

  .wordmark {
    font-family: "Anton", "Oswald", sans-serif;
    font-weight: 400;
    text-transform: uppercase;
    line-height: 1;
    text-align: left;
  }
  .wordmark__name {
    display: block;
    font-size: 62px;
    letter-spacing: 1px;
  }
  .wordmark__tagline {
    display: block;
    font-size: 19px;
    letter-spacing: 1px;
    margin-top: 4px;
  }

  .divider {
    position: absolute;
    left: 262px;
    top: 72px;
    width: 1px;
    height: 150px;
    background: var(--rule-blue);
  }

  .contact {
    position: absolute;
    left: 284px;
    top: 64px;
    color: var(--brand-blue);
    font-family: "Montserrat", sans-serif;
    font-size: 13.5px;
    line-height: 1.35;
  }
  .contact__name {
    font-family: "Anton", "Oswald", sans-serif;
    font-size: 20px;
    letter-spacing: 1px;
    text-transform: uppercase;
    word-spacing: 6px;
    line-height: 1.1;
  }
  .contact__role {
    text-transform: uppercase;
    letter-spacing: 0.5px;
    margin-bottom: 10px;
  }
  .contact__address { margin-bottom: 10px; }
  .contact__line {
    display: flex;
    align-items: center;
    gap: 6px;
  }
  .contact__icon {
    width: 11px;
    height: 11px;
    flex: none;
  }
</style>
</head>
<body>
<main class="canvas">

  <section class="card card--front" aria-label="Business card front">
    <div class="wordmark">
      <span class="wordmark__name">Rally</span>
      <span class="wordmark__tagline">Functional Fitness</span>
    </div>
  </section>

  <section class="card card--back" aria-label="Business card back">
    <div class="wordmark">
      <span class="wordmark__name">Rally</span>
      <span class="wordmark__tagline">Functional Fitness</span>
    </div>

    <div class="divider"></div>

    <div class="contact">
      <p class="contact__name">Marcus Delaney</p>
      <p class="contact__role">Expert Coaches</p>
      <p class="contact__address">472 Halvern Drive<br>Decatur GA 30041</p>
      <p class="contact__line">
        <svg class="contact__icon" viewBox="0 0 24 24" aria-hidden="true">
          <path fill="currentColor" d="M6.6 10.8a15.1 15.1 0 0 0 6.6 6.6l2.2-2.2a1 1 0 0 1 1-.25 11.4 11.4 0 0 0 3.6.57 1 1 0 0 1 1 1V20a1 1 0 0 1-1 1A17 17 0 0 1 3 4a1 1 0 0 1 1-1h3.5a1 1 0 0 1 1 1c0 1.25.2 2.45.57 3.57a1 1 0 0 1-.25 1z"/>
        </svg>
        404.555.0187
      </p>
      <p class="contact__line">
        <svg class="contact__icon" viewBox="0 0 24 24" aria-hidden="true">
          <circle cx="12" cy="12" r="10" fill="none" stroke="currentColor" stroke-width="2.4"/>
          <path d="M2 12h20M12 2c3 3 3 17 0 20M12 2c-3 3-3 17 0 20" fill="none" stroke="currentColor" stroke-width="1.8"/>
        </svg>
        www.rallygym.example
      </p>
    </div>
  </section>

</main>
</body>
</html>
```